Local Roofing/Construction company business needs new biz card design

We need a new business card design, current cards are from the start of this operation and generic at best. We are a local Construction Company (General Contractor) with a majority of our work originating from insurance claims-exterior finish work is the main focus (Roofs-Siding-Gutters etc). Heavily involved with homeowners and the low ball offers they receive from insurance company's after a insurable event takes place. I have attached some of our original logo file(s) below.

```html
<!DOCTYPE html>
<html lang="en">
<head>
<meta charset="utf-8">
<title>Oakline Construction — Business Card</title>
<link href="https://fonts.googleapis.com/css2?family=Montserrat:wght@400;500;700;800&display=swap" rel="stylesheet">
<style>
  :root {
    --page: #141416;
    --card: #1e1e20;
    --accent: #2fd37a;
    --text-light: #f2f2f2;
    --emboss: #0d0d0e;
    --emboss-edge: #2a2a2c;
  }
  * { margin: 0; padding: 0; box-sizing: border-box; }
  html, body {
    width: 1200px; height: 900px; overflow: hidden;
    background: var(--page);
    font-family: "Montserrat", sans-serif;
  }
  .stage {
    width: 1200px; height: 900px;
    display: flex; flex-direction: column; align-items: center; justify-content: center;
    gap: 56px;
  }
  .card {
    position: relative;
    width: 600px; height: 343px;
    background: var(--card);
    border-radius: 22px;
    border-bottom: 5px solid var(--accent);
    overflow: hidden;
  }
  /* Front */
  .card-front { display: flex; align-items: center; justify-content: center; gap: 18px; }
  .front-mark {
    width: 54px; height: 54px; background: var(--emboss);
    box-shadow: 0 1px 0 var(--emboss-edge);
  }
  .front-name {
    color: var(--emboss);
    font-weight: 800; font-size: 38px; line-height: 1.05; letter-spacing: 1px;
    text-shadow: 0 1px 0 var(--emboss-edge);
  }
  /* Back */
  .brand-block {
    position: absolute; top: 28px; right: 30px;
    display: flex; align-items: center; gap: 12px;
  }
  .brand-square {
    width: 118px; height: 104px; background: var(--accent); border-radius: 14px;
  }
  .brand-name {
    color: var(--accent); font-weight: 800; font-size: 17px; line-height: 1.15;
    letter-spacing: 0.5px; text-transform: uppercase;
  }
  .person { position: absolute; left: 36px; top: 192px; }
  .person-name { color: var(--accent); font-weight: 700; font-size: 27px; }
  .divider {
    position: absolute; left: 36px; right: 30px; top: 232px;
    height: 1px; background: var(--accent);
  }
  .person-role {
    position: absolute; left: 36px; top: 240px;
    color: var(--text-light); font-size: 15px; font-weight: 400;
  }
  .contacts { position: absolute; left: 36px; top: 268px; list-style: none; }
  .contacts li {
    display: flex; align-items: center; gap: 10px;
    color: var(--text-light); font-size: 13.5px; line-height: 20px;
  }
  .contacts svg { width: 12px; height: 12px; fill: var(--accent); flex: none; }
  .address {
    position: absolute; right: 30px; top: 250px; text-align: right;
    color: var(--text-light); font-size: 13.5px; line-height: 20px;
  }
</style>
</head>
<body>
<main class="stage">
  <section class="card card-front" aria-label="Card front">
    <div class="front-mark"></div>
    <div class="front-name">OAKLINE<br>CONSTRUCTION</div>
  </section>

  <section class="card card-back" aria-label="Card back">
    <div class="brand-block">
      <div class="brand-name">Oakline<br>Construction</div>
      <div class="brand-square"></div>
    </div>

    <div class="person"><h1 class="person-name">Daniel Moreau</h1></div>
    <div class="divider"></div>
    <p class="person-role">Owner</p>

    <ul class="contacts">
      <li>
        <svg viewBox="0 0 24 24"><path d="M6.6 10.8a15 15 0 0 0 6.6 6.6l2.2-2.2a1 1 0 0 1 1-.25 11.4 11.4 0 0 0 3.6.57 1 1 0 0 1 1 1V20a1 1 0 0 1-1 1A17 17 0 0 1 3 4a1 1 0 0 1 1-1h3.5a1 1 0 0 1 1 1c0 1.25.2 2.45.57 3.57a1 1 0 0 1-.25 1z"/></svg>
        555-014-2290
      </li>
      <li>
        <svg viewBox="0 0 24 24"><path d="M2 5h20v14H2zm2 2v.5l8 5 8-5V7l-8 5z"/></svg>
        info@oaklinebuild.com
      </li>
      <li>
        <svg viewBox="0 0 24 24"><path d="M12 2a10 10 0 1 0 0 20 10 10 0 0 0 0-20zm0 3a7 7 0 0 1 6.7 5H15a12 12 0 0 0-1.5-4.8A7 7 0 0 1 12 5zm-1.5.2A12 12 0 0 0 9 10H5.3a7 7 0 0 1 5.2-4.8zM5.3 14H9a12 12 0 0 0 1.5 4.8A7 7 0 0 1 5.3 14zm8.2 4.8A12 12 0 0 0 15 14h3.7a7 7 0 0 1-5.2 4.8z"/></svg>
        www.oaklinebuild.com
      </li>
    </ul>

    <p class="address">42 Birch Hollow Rd<br>Fairview, MO 63000</p>
  </section>
</main>
</body>
</html>
```